Property management company looking for modern card design

We at Blue Heron Partners provides property management services for its residential and commercial properties, with expertise in all categories of multifamily, industrial and office projects throughout California.

We need a business card design that is professional and modern designed business card. In our field, clients get hundreds of business cards, we would like our card to stand out.

Please avoid small print.

Target Market(s)

Professionals and high end clients

Industry/Entity Type

Financial Planning

Contact Information for Business Card

Company Name: Blue Heron Partners, Name, email, license #, phone number, website blueheronpartners.com

Font styles to use
Sans Serif

Requirements
Must have
• The card design needs to be adaptable because there is a possibly we will be expanding into different sectors other than real estate. The card design should be focused on financial planning and asset management.
Nice to have
• Modern and simple business card. Eye catching. Non-standard size/shaped cards would be great.
• blueheronpartners.com
Should not have
• Too many bright color or any pictures or shapes of real estate stuff.

```html
<!DOCTYPE html>
<html lang="en">
<head>
<meta charset="utf-8">
<title>Blue Heron Partners – Business Card</title>
<link href="https://fonts.googleapis.com/css2?family=PT+Sans:wght@400;700&family=Arimo:wght@400&display=swap" rel="stylesheet">
<style>
  :root {
    --backdrop: #d9c6ad;
    --card: #f1ede2;
    --brand-red: #c8102e;
    --deep-red: #9e1020;
    --ink: #2a2a2a;
  }
  * { margin: 0; padding: 0; box-sizing: border-box; }
  html, body { width: 1200px; height: 823px; overflow: hidden; }
  body {
    background: var(--backdrop);
    display: flex;
    align-items: center;
    justify-content: center;
  }
  .business-card {
    position: relative;
    width: 960px;
    height: 548px;
    background: var(--card);
    box-shadow: 0 10px 30px rgba(80, 60, 40, 0.25);
  }
  .brand {
    position: absolute;
    left: 90px;
    top: 110px;
    display: flex;
    flex-direction: column;
    align-items: center;
    gap: 28px;
  }
  .brand-mark {
    width: 200px;
    height: 200px;
    border-radius: 50%;
    background: var(--deep-red);
  }
  .brand-name {
    font-family: "PT Sans", sans-serif;
    font-weight: 400;
    font-size: 48px;
    letter-spacing: 0.18em;
    color: var(--brand-red);
    text-transform: uppercase;
  }
  .contact {
    position: absolute;
    right: 80px;
    top: 130px;
    text-align: right;
  }
  .contact-name {
    font-family: "PT Sans", sans-serif;
    font-size: 40px;
    color: var(--brand-red);
    margin-bottom: 44px;
  }
  .contact-list { list-style: none; }
  .contact-item {
    display: flex;
    justify-content: flex-end;
    align-items: center;
    gap: 12px;
    font-family: "Arimo", sans-serif;
    font-size: 28px;
    color: var(--ink);
    line-height: 1.3;
  }
  .contact-icon { width: 26px; height: 26px; flex: none; }
  .contact-icon.blank { visibility: hidden; }
  .license {
    position: absolute;
    right: 80px;
    bottom: 90px;
    font-family: "Arimo", sans-serif;
    font-size: 28px;
    color: #111;
  }
</style>
</head>
<body>
  <article class="business-card">
    <div class="brand">
      <div class="brand-mark"></div>
      <div class="brand-name">Blue Heron</div>
    </div>

    <div class="contact">
      <h1 class="contact-name">Nolan Pierce</h1>
      <ul class="contact-list">
        <li class="contact-item">555-014-2290
          <svg class="contact-icon" viewBox="0 0 26 26" aria-hidden="true">
            <rect width="26" height="26" rx="5" fill="var(--brand-red)"/>
            <path d="M8 7c-1 1-1 3 0 5 2 3 4 5 7 7 2 1 4 1 5 0l-2-3-2 1c-2-1-4-3-5-5l1-2z" fill="#fff"/>
          </svg>
        </li>
        <li class="contact-item">hello@heron.com
          <svg class="contact-icon" viewBox="0 0 26 26" aria-hidden="true">
            <rect width="26" height="26" rx="5" fill="var(--brand-red)"/>
            <rect x="6" y="8" width="14" height="10" fill="none" stroke="#fff" stroke-width="1.6"/>
            <path d="M6 8l7 6 7-6" fill="none" stroke="#fff" stroke-width="1.6"/>
          </svg>
        </li>
        <li class="contact-item">blueheronpartners.com
          <svg class="contact-icon" viewBox="0 0 26 26" aria-hidden="true">
            <rect width="26" height="26" rx="5" fill="var(--brand-red)"/>
            <circle cx="13" cy="13" r="7" fill="none" stroke="#fff" stroke-width="1.5"/>
            <ellipse cx="13" cy="13" rx="3" ry="7" fill="none" stroke="#fff" stroke-width="1.2"/>
            <path d="M6 13h14" stroke="#fff" stroke-width="1.2"/>
          </svg>
        </li>
      </ul>
    </div>

    <p class="license">Lic : 40918263</p>
  </article>
</body>
</html>
```